Cover for Lindqvist Review 2023 using photo provided

I need a cover (front and back) designed for the 2023 version of the Lindqvist Review, using the photo attached (may2019_) of an Inuit hunter.

I want the photo to be prominent and close to the original look (ie not too much change to the the photo, except maybe tone or shading to make it look more like a book cover).

The title should be prominent: Coastal Weavers: Trade, Craft, Memory and Exchange Across Shores.
The authors should be listed: Tapio Korhola, Marcus Dell & Celeste Varga-Moine, eds.
The Lindqvist Review 2023 logo should be on the front, and the LR2023 logo should be on the spine. The Lindqvist Review and Caldera Gateway logos should be on the back cover, which can otherwise be simple.
Back cover should also include: ISSN 4751-3096

I have included the photo for this year's cover (Inuit hunter), logos, as well as the last two covers for reference.

• A4 front and back cover with 26 mm spine

```html
<!DOCTYPE html>
<html lang="en">
<head>
<meta charset="utf-8">
<title>Lindqvist Review 2023 — Cover Spread</title>
<link rel="stylesheet" href="https://fonts.googleapis.com/css2?family=Archivo:wght@700&family=Tinos:wght@700&family=Red+Hat+Display:wght@600&display=swap">
<style>
  :root {
    --page-bg: #1e2238;
    --sky-top: #6b99d1;
    --sky-bottom: #92b2d8;
    --navy: #1f3370;
    --ice-band: #a9c3e6;
    --snow: #e5e6e9;
    --ink: #1b1f2e;
    --white: #ffffff;
    --gateway-blue: #23468f;
  }
  * { margin: 0; padding: 0; box-sizing: border-box; }
  html, body { width: 906px; height: 1200px; overflow: hidden; }
  body { background: var(--page-bg); position: relative; }

  .cover-spread {
    position: absolute;
    left: 0; top: 0;
    width: 1129px; height: 752px;
    transform-origin: 0 0;
    transform: translate(18px, 310px) scale(0.77);
    background: var(--snow);
    overflow: hidden;
    box-shadow: 0 30px 70px rgba(0,0,0,0.45);
  }

  .sky { position: absolute; left: 0; top: 0; width: 100%; height: 278px;
    background: linear-gradient(180deg, var(--sky-top) 0%, var(--sky-top) 40%, var(--sky-bottom) 100%); }
  .navy-band { position: absolute; left: 0; top: 278px; width: 100%; height: 170px; background: var(--navy); }
  .mountain-strip { position: absolute; left: 0; top: 380px; width: 840px; height: 68px;
    background: linear-gradient(180deg, #2a3656 0%, #161d33 60%, #1c2540 100%); }
  .ice-band { position: absolute; left: 0; top: 448px; width: 100%; height: 50px; background: var(--ice-band); }
  .snow { position: absolute; left: 0; top: 498px; width: 100%; height: 254px;
    background: linear-gradient(180deg, #eeeff1 0%, var(--snow) 100%); }

  .photo-hunter { position: absolute; left: 915px; top: 252px; width: 180px; height: 360px;
    background: linear-gradient(180deg, #2b2d36 0%, #3a3c44 40%, #d9d6cc 62%, #cfcbc0 85%, #3a3a3e 100%);
    opacity: 0.85; }
  .photo-seal { position: absolute; left: 640px; top: 548px; width: 250px; height: 40px;
    background: linear-gradient(90deg, #6d6a62 0%, #57544e 50%, #7a776f 100%); opacity: 0.8; }

  .name { position: absolute; font-family: "Archivo", sans-serif; font-weight: 700; color: var(--white); line-height: 0.95; }
  .name--front { left: 636px; top: 52px; font-size: 60px; letter-spacing: -0.5px; }
  .name--back { left: 184px; top: 308px; font-size: 29px; letter-spacing: -0.3px; }
  .name--spine { left: 548px; top: 52px; font-size: 13px; }

  .title { position: absolute; left: 638px; top: 312px; font-family: "Tinos", serif; font-weight: 700;
    color: var(--white); font-size: 48px; line-height: 0.88; letter-spacing: 0.5px; }
  .subtitle { position: absolute; left: 636px; top: 452px; font-family: "Red Hat Display", sans-serif; font-weight: 600;
    color: var(--ink); font-size: 18px; line-height: 1.1; letter-spacing: 0.3px; }
  .editors { position: absolute; left: 636px; top: 666px; font-family: "Red Hat Display", sans-serif; font-weight: 600;
    color: var(--ink); font-size: 18px; line-height: 1.25; letter-spacing: 0.3px; }
  .issn { position: absolute; left: 322px; top: 690px; font-family: "Red Hat Display", sans-serif; font-weight: 600;
    color: var(--ink); font-size: 21px; letter-spacing: 0.3px; }

  .publisher { position: absolute; left: 50px; top: 690px; display: flex; align-items: center; gap: 8px;
    font-family: "Red Hat Display", sans-serif; font-weight: 600; font-size: 18px; color: var(--gateway-blue); }
  .publisher .mark { width: 12px; height: 12px; border-radius: 50%; background: var(--gateway-blue); }
</style>
</head>
<body>
  <section class="cover-spread" aria-label="Lindqvist Review 2023 cover spread: back, spine and front">
    <div class="sky"></div>
    <div class="navy-band"></div>
    <div class="mountain-strip" role="img" aria-label="Photo strip of dark snow-streaked mountain ridge on the horizon"></div>
    <div class="ice-band"></div>
    <div class="snow"></div>

    <div class="photo-seal" role="img" aria-label="Photo of a seal lying on the sea ice"></div>
    <div class="photo-hunter" role="img" aria-label="Photo of a hunter in fur trousers and boots standing on the ice holding a rifle"></div>

    <!-- back cover -->
    <p class="name name--back">LINDQVIST<br>REVIEW 2023</p>
    <div class="publisher"><span class="mark"></span><span>Caldera Gateway</span></div>
    <p class="issn">ISSN 4751-3096</p>

    <!-- spine -->
    <p class="name name--spine">LR2023</p>

    <!-- front cover -->
    <p class="name name--front">LINDQVIST<br>REVIEW 2023</p>
    <h1 class="title">COASTAL<br>WEAVERS:</h1>
    <p class="subtitle">TRADE, CRAFT, MEMORY AND<br>EXCHANGE ACROSS SHORES.</p>
    <p class="editors">TAPIO KORHOLA, MARCUS DELL &amp;<br>CELESTE VARGA-MOINE, EDS.</p>
  </section>
</body>
</html>
```